Lucky Harbour Fun Casino Entertainment

Looking to update my business card and make it look more modern, stand out and eye catching.
We are are fun casino business in Australia (primarily Sydney). Blackjack and Roulette are our most popular games although we have pretty much every game available for hire that you would find in a real casino. The final design would need to be sleek and appeal to the more upmarket corporate sector.
We mainly cater for Corporate Events, Private Parties, Fundraising Events, Team Building, Poker Tournaments
I think I'd prefer the colour Black.

Target Market(s)

High-end Corporate

Industry/Entity Type

Events

Contact Information for Business Card

Rob Kendall
Director
1300 482 617
0433 728 591
info@luckyharbour.com.au
www.luckyharbour.com.au
Facebook & Instagram @luckyharbourevents (proper social icons preferred)

Colors
000000
0255a3

Requirements
Must have
• Front side:
• Logo
• Contact details
• 'Australia's #1 Fun Casino Specialists'
• Back:
• Logo
Nice to have
• Back:
• Corporate Events
• Private Parties
• Poker Tournaments
• Fundraising
• Props & Theming
• Photo Booth
• Horse Racing Events
• The Vegas Sign attached, maybe on the back of the card in the background...?

```html
<!DOCTYPE html>
<html lang="en">
<head>
<meta charset="utf-8">
<title>Lucky Harbour – Business Card</title>
<link href="https://fonts.googleapis.com/css2?family=Open+Sans:wght@400;600;700&family=Great+Vibes&display=swap" rel="stylesheet">
<style>
  :root {
    --stage: #2b2e33;
    --card-white: #ffffff;
    --card-black: #1a1a1b;
    --band-grey: #3a3a3c;
    --accent: #f7a21b;
    --accent-deep: #f08c00;
    --ink: #2a2a2a;
    --ink-soft: #6d6d6d;
    --rule: #c9c9c9;
  }
  * { box-sizing: border-box; margin: 0; padding: 0; }
  html, body { width: 1200px; height: 900px; overflow: hidden; }
  body {
    background: var(--stage);
    font-family: "Open Sans", sans-serif;
    position: relative;
  }
  .card {
    position: absolute;
    left: 290px;
    width: 620px;
    height: 354px;
    border-radius: 22px;
    overflow: hidden;
  }
  /* Front */
  .card-front { top: 56px; background: var(--card-white); }
  .front-left {
    position: absolute; left: 30px; top: 80px; width: 250px;
    display: flex; flex-direction: column; align-items: center; gap: 18px;
  }
  .front-brand { display: flex; align-items: center; gap: 12px; }
  .brand-dot {
    width: 34px; height: 34px; border-radius: 50%;
    background: var(--accent); flex: none;
  }
  .brand-name {
    font-weight: 700; font-size: 24px; line-height: 1.05;
    color: var(--card-black); letter-spacing: 0.5px;
  }
  .tagline {
    font-family: "Great Vibes", cursive;
    font-size: 24px; color: var(--ink);
  }
  .front-tagline { font-size: 19px; white-space: nowrap; }
  .front-divider {
    position: absolute; left: 292px; top: 150px;
    width: 1.5px; height: 150px; background: var(--rule);
  }
  .person { position: absolute; right: 40px; top: 38px; text-align: right; }
  .person-name { font-size: 27px; font-weight: 700; color: var(--accent); }
  .person-role { font-size: 15px; color: var(--ink-soft); margin-top: -2px; }
  .person-rule {
    width: 120px; height: 2px; margin: 6px 0 0 auto;
    background: linear-gradient(90deg, var(--accent), var(--card-black));
  }
  .contact {
    position: absolute; left: 312px; top: 150px;
    list-style: none; font-size: 14px; color: var(--ink-soft);
  }
  .contact li { display: flex; align-items: flex-start; gap: 8px; margin-bottom: 5px; }
  .contact .address { color: var(--accent); font-weight: 700; font-size: 15px; line-height: 1.3; margin-bottom: 8px; }
  .icon { width: 16px; height: 16px; flex: none; margin-top: 1px; }
  .front-edge { position: absolute; left: 0; right: 0; bottom: 0; height: 14px; }
  .edge-black { position: absolute; left: 0; bottom: 8px; width: 62%; height: 3px; background: var(--card-black); }
  .edge-accent {
    position: absolute; left: 18%; bottom: 0; width: 30%; height: 6px;
    background: linear-gradient(90deg, var(--accent-deep), #ffd23a);
  }
  /* Back */
  .card-back {
    top: 490px;
    background: radial-gradient(circle at 62% 42%, #2f2f31 0%, var(--card-black) 60%);
  }
  .back-glow {
    position: absolute; left: 250px; top: -40px; width: 340px; height: 340px;
    border-radius: 50%;
    background: radial-gradient(circle, rgba(247,162,27,0.10), rgba(247,162,27,0) 70%);
  }
  .back-brand {
    position: absolute; left: 0; right: 0; top: 68px;
    display: flex; justify-content: center; align-items: center; gap: 14px;
  }
  .back-brand .brand-name { color: var(--accent); font-size: 36px; }
  .back-brand .brand-dot { width: 44px; height: 44px; }
  .back-tagline {
    position: absolute; left: 0; right: 0; top: 140px; text-align: center;
    color: #e6e6e6; font-size: 30px;
  }
  .services-band {
    position: absolute; left: 0; right: 0; top: 214px; height: 84px;
    background: rgba(70,70,72,0.75);
    display: flex; flex-direction: column; justify-content: center; align-items: center; gap: 6px;
  }
  .services { display: flex; gap: 8px; align-items: center; font-size: 14px; color: var(--accent); }
  .services .sep { width: 7px; height: 7px; border: 1.5px solid var(--accent); border-radius: 50%; }
</style>
</head>
<body>

<section class="card card-front" aria-label="Business card front">
  <div class="front-left">
    <div class="front-brand">
      <span class="brand-dot"></span>
      <span class="brand-name">LUCKY<br>HARBOUR</span>
    </div>
    <p class="tagline front-tagline">Australia's #1 Fun Casino Specialists</p>
  </div>
  <div class="front-divider" aria-hidden="true"></div>

  <div class="person">
    <p class="person-name">Rob Kendall</p>
    <p class="person-role">Director</p>
    <div class="person-rule"></div>
  </div>

  <ul class="contact">
    <li class="address">
      <svg class="icon" viewBox="0 0 16 16" aria-hidden="true"><circle cx="8" cy="8" r="7.2" fill="none" stroke="var(--accent)" stroke-width="1.4"/><path d="M8 3.5a2.8 2.8 0 0 0-2.8 2.8C5.2 8.4 8 12 8 12s2.8-3.6 2.8-5.7A2.8 2.8 0 0 0 8 3.5z" fill="var(--accent)"/></svg>
      <span>5/218 Harbour Street,<br>Rosehill 2142</span>
    </li>
    <li>
      <svg class="icon" viewBox="0 0 16 16" aria-hidden="true"><circle cx="8" cy="8" r="7.2" fill="none" stroke="var(--accent)" stroke-width="1.4"/><path d="M5.2 4.5l1.6-.3.9 2-1 .8a5 5 0 0 0 2.3 2.3l.8-1 2 .9-.3 1.6c-3.6.3-6.6-2.7-6.3-6.3z" fill="var(--accent)"/></svg>
      <span>1300 482 617</span>
      <svg class="icon" viewBox="0 0 16 16" aria-hidden="true"><circle cx="8" cy="8" r="7.2" fill="none" stroke="var(--accent)" stroke-width="1.4"/><rect x="5.5" y="3.8" width="5" height="8.4" rx="1" fill="var(--accent)"/></svg>
      <span>0433 728 591</span>
    </li>
    <li>
      <svg class="icon" viewBox="0 0 16 16" aria-hidden="true"><circle cx="8" cy="8" r="7.2" fill="none" stroke="var(--accent)" stroke-width="1.4"/><rect x="4" y="5" width="8" height="6" fill="none" stroke="var(--accent)" stroke-width="1.2"/><path d="M4 5l4 3.3L12 5" fill="none" stroke="var(--accent)" stroke-width="1.2"/></svg>
      <span>info@luckyharbour.com.au</span>
    </li>
    <li>
      <svg class="icon" viewBox="0 0 16 16" aria-hidden="true"><circle cx="8" cy="8" r="7.2" fill="none" stroke="var(--accent)" stroke-width="1.4"/><circle cx="8" cy="8" r="3.8" fill="none" stroke="var(--accent)" stroke-width="1.1"/><line x1="4.2" y1="8" x2="11.8" y2="8" stroke="var(--accent)" stroke-width="1.1"/></svg>
      <span>www.luckyharbour.com.au</span>
    </li>
    <li>
      <svg class="icon" viewBox="0 0 16 16" aria-hidden="true"><circle cx="8" cy="8" r="7.2" fill="var(--accent)"/></svg>
      <span>@luckyharbourevents</span>
    </li>
    <li>
      <svg class="icon" viewBox="0 0 16 16" aria-hidden="true"><circle cx="8" cy="8" r="7.2" fill="var(--accent)"/></svg>
      <span>@luckyharbourevents</span>
    </li>
  </ul>

  <div class="front-edge">
    <div class="edge-black"></div>
    <div class="edge-accent"></div>
  </div>
</section>

<section class="card card-back" aria-label="Business card back">
  <div class="back-glow"></div>
  <div class="back-brand">
    <span class="brand-dot"></span>
    <span class="brand-name">LUCKY HARBOUR</span>
  </div>
  <p class="tagline back-tagline">Australia's #1 Fun Casino Specialists</p>
  <div class="services-band">
    <div class="services">
      <span class="sep"></span><span>Corporate Events</span>
      <span class="sep"></span><span>Private Parties</span>
      <span class="sep"></span><span>Poker Tournaments</span>
    </div>
    <div class="services">
      <span class="sep"></span><span>Fundraising</span>
      <span class="sep"></span><span>Props &amp; Theming</span>
      <span class="sep"></span><span>Photo Booth</span>
      <span class="sep"></span><span>Horse Racing Events</span>
    </div>
  </div>
</section>

</body>
</html>
```